Velmora Cabinets Letter Head and Email Signature

Hi
I would love a design package for a letterhead, email signature, even update my business card if you like if you can come up with a great idea for my new high end cabinet shop. Velmora Cabinets brings timeless craftsmanship to modern interiors, specializing in high end, custom cabinetry designed for architects and interior designers.

Target Market(s)

high end, luxury market

Industry/Entity Type

cabinet making

Requirements
Must have
• my colours of logo as the theme

```html
<!DOCTYPE html>
<html lang="en">
<head>
<meta charset="utf-8">
<title>Velmora Cabinets – Email Signature</title>
<link rel="stylesheet" href="https://fonts.googleapis.com/css2?family=Montserrat:wght@400;500;800&display=swap">
<style>
  :root {
    --page: #ffffff;
    --ink: #000000;
    --panel: #1a1a1a;
    --green: #4a7c48;
    --white: #ffffff;
  }
  * { margin: 0; padding: 0; box-sizing: border-box; }
  html, body {
    width: 1200px;
    height: 726px;
    overflow: hidden;
    background: var(--page);
    font-family: "Montserrat", Arial, sans-serif;
  }
  .signature {
    position: absolute;
    left: 90px;
    top: 193px;
    width: 1021px;
    height: 341px;
    background: var(--ink);
    overflow: hidden;
  }
  .signature__shapes {
    position: absolute;
    inset: 0;
  }
  .person {
    position: absolute;
    left: 454px;
    top: 52px;
  }
  .person__name {
    font-weight: 800;
    font-size: 33px;
    line-height: 1;
    color: var(--green);
    letter-spacing: -0.2px;
  }
  .person__role {
    margin-top: 10px;
    font-weight: 500;
    font-size: 18px;
    line-height: 1;
    color: var(--white);
    letter-spacing: 2.6px;
  }
  .brand {
    position: absolute;
    left: 66px;
    top: 212px;
    display: flex;
    align-items: center;
    gap: 14px;
  }
  .brand__mark {
    width: 34px;
    height: 34px;
    background: var(--green);
  }
  .brand__name {
    font-weight: 500;
    font-size: 24px;
    color: var(--white);
    letter-spacing: 1.5px;
  }
  .contacts {
    position: absolute;
    left: 453px;
    top: 184px;
    list-style: none;
  }
  .contacts__item {
    display: flex;
    align-items: center;
    height: 24px;
    margin-bottom: 11.5px;
    font-size: 20px;
    font-weight: 500;
    color: var(--white);
  }
  .contacts__icon {
    width: 18px;
    height: 18px;
    margin-right: 9px;
    flex: none;
  }
</style>
</head>
<body>
  <section class="signature" aria-label="Velmora Cabinets email signature">
    <svg class="signature__shapes" width="1021" height="341" viewBox="0 0 1021 341" aria-hidden="true">
      <defs>
        <linearGradient id="panel-fade" x1="0" x2="1" y1="0" y2="0">
          <stop offset="0" stop-color="#000000"/>
          <stop offset="0.45" stop-color="#1a1a1a"/>
          <stop offset="1" stop-color="#1a1a1a"/>
        </linearGradient>
      </defs>
      <polygon class="band-top" points="362,0 1021,0 1021,22 350,22" fill="var(--green)"/>
      <polygon class="rule-white" points="90,84 297,84 343,0 358,0 305,98 90,98" fill="var(--white)"/>
      <polygon class="panel" points="0,150 980,150 870,341 0,341" fill="url(#panel-fade)"/>
      <polygon class="corner-white" points="924,278 1021,278 1021,341 870,341" fill="var(--white)"/>
      <polygon class="rule-green" points="980,150 996,150 902,318 682,318 682,304 893,304" fill="var(--green)"/>
    </svg>

    <div class="person">
      <p class="person__name">Dorian Halvek</p>
      <p class="person__role">Director Craftsman</p>
    </div>

    <div class="brand">
      <span class="brand__mark" aria-hidden="true"></span>
      <span class="brand__name">Velmora Cabinets</span>
    </div>

    <ul class="contacts">
      <li class="contacts__item">
        <svg class="contacts__icon" viewBox="0 0 18 18" aria-hidden="true">
          <circle cx="9" cy="9" r="9" fill="var(--green)"/>
          <path d="M6 4.5c.5-.3 1-.2 1.3.3l.8 1.4c.2.4.1.9-.3 1.2l-.5.4c.5 1.1 1.3 1.9 2.4 2.4l.4-.5c.3-.4.8-.5 1.2-.3l1.4.8c.5.3.6.8.3 1.3-.7 1.2-1.8 1.5-3 .9-2-1-3.6-2.6-4.6-4.6-.6-1.2-.3-2.3.6-3.3z" fill="var(--white)"/>
        </svg>
        0400 123 456
      </li>
      <li class="contacts__item">
        <svg class="contacts__icon" viewBox="0 0 18 18" aria-hidden="true">
          <circle cx="9" cy="9" r="9" fill="var(--green)"/>
          <rect x="5" y="6" width="8" height="6" fill="var(--white)"/>
          <path d="M5 6l4 3.3L13 6" fill="none" stroke="var(--green)" stroke-width="0.9"/>
        </svg>
        dorianh@velmoracabinets.com.au
      </li>
      <li class="contacts__item">
        <svg class="contacts__icon" viewBox="0 0 18 18" aria-hidden="true">
          <circle cx="9" cy="9" r="9" fill="var(--green)"/>
          <rect x="5.5" y="5.5" width="7" height="7" fill="none" stroke="var(--white)" stroke-width="1.2"/>
        </svg>
        @velmora.cabinets
      </li>
    </ul>
  </section>
</body>
</html>
```